Design of retail home garden product

We are searching for a modern and out of the box but practical design for our home garden product. The example product is called mossvanish and removes green pollution on walls, buildings, and pavements.
We would like a futuristic design that we can use for our whole product line home garden, which should emphasize the future, eco, bright colors, modern shapes, clear images and an appealing look for the retail market. Currently we have three products in our home garden line, a green pollution remover, nanotechnology spray for masks and a natural bug cleaner.

Target Market(s)

Retail

Industry/Entity Type

Retail

Font styles to use
Sans Serif

Requirements
Must have
• Modern design, retail design, see in 1 look what the product does, home garden look and feel
Nice to have
• Icons, practical items that shows what the product does, modern logo design
Should not have
• Outdated design

```html
<!DOCTYPE html>
<html lang="nl">
<head>
<meta charset="utf-8">
<title>Moss Vanish – Hofwerk</title>
<link rel="stylesheet" href="https://fonts.googleapis.com/css2?family=Great+Vibes&family=Roboto+Condensed:wght@400;700&display=swap">
<style>
  :root {
    --leaf-dark: #1f8a3a;
    --leaf: #3aa935;
    --lime: #9cc71c;
    --lime-soft: #8dc63f;
    --lime-light: #c8dc2a;
    --ink: #111111;
    --paper: #ffffff;
    --hazard: #d0021b;
  }
  html, body { margin: 0; padding: 0; overflow: hidden; background: var(--paper); }
  .label {
    position: relative;
    width: 1200px;
    height: 811px;
    overflow: hidden;
    background: var(--paper);
    font-family: "Roboto Condensed", Arial, sans-serif;
    color: var(--ink);
  }
  .swooshes { position: absolute; inset: 0; }
  .brand {
    position: absolute;
    left: 470px;
    top: 110px;
    display: flex;
    align-items: center;
    gap: 14px;
    font-weight: 700;
    font-size: 80px;
    line-height: 1;
    color: var(--leaf);
    letter-spacing: -1px;
  }
  .brand-dot {
    width: 30px;
    height: 30px;
    border-radius: 50%;
    background: var(--leaf);
  }
  .product-name {
    position: absolute;
    left: 0;
    top: 0;
    margin: 0;
    font-family: "Great Vibes", cursive;
    font-weight: 400;
    line-height: 1;
  }
  .product-name span { position: absolute; white-space: nowrap; }
  .product-name .line-one {
    left: 270px;
    top: 260px;
    font-size: 250px;
    color: var(--lime-soft);
  }
  .product-name .line-two {
    left: 130px;
    top: 450px;
    font-size: 270px;
    color: var(--leaf);
  }
  .hazard { position: absolute; left: 796px; top: 46px; width: 34px; height: 34px; }
  .instructions {
    position: absolute;
    left: 847px;
    top: 56px;
    width: 335px;
    font-size: 11px;
    line-height: 15.5px;
    text-align: justify;
  }
  .instructions p { margin: 0 0 15px; }
  .instructions h2 { font-size: 11px; margin: 0; font-weight: 700; }
  .instructions .gap { margin-top: 26px; }
  .instructions strong { font-weight: 700; }
  .registration {
    position: absolute;
    left: 998px;
    top: 772px;
    font-size: 12px;
  }
</style>
</head>
<body>
<div class="label">
  <svg class="swooshes" width="1200" height="811" viewBox="0 0 1200 811" aria-hidden="true">
    <defs>
      <linearGradient id="cornerGrad" x1="0" y1="0" x2="1" y2="1">
        <stop offset="0" stop-color="#1f8a3a"/>
        <stop offset="0.55" stop-color="#3aa935"/>
        <stop offset="1" stop-color="#c8dc2a"/>
      </linearGradient>
      <linearGradient id="bandGrad" x1="0" y1="1" x2="1" y2="0">
        <stop offset="0" stop-color="#c8dc2a"/>
        <stop offset="0.6" stop-color="#9cc71c"/>
        <stop offset="1" stop-color="#3aa935"/>
      </linearGradient>
      <linearGradient id="bandDark" x1="0" y1="1" x2="1" y2="0">
        <stop offset="0" stop-color="#3aa935"/>
        <stop offset="1" stop-color="#1f8a3a"/>
      </linearGradient>
    </defs>
    <path d="M0,0 H420 C300,70 150,200 70,420 L0,580 Z" fill="url(#cornerGrad)"/>
    <path d="M0,0 H250 C160,60 80,160 30,300 L0,380 Z" fill="#1f8a3a" opacity="0.6"/>
    <path d="M220,811 C520,700 900,560 1200,370 V811 Z" fill="url(#bandGrad)"/>
    <path d="M240,811 C540,712 920,580 1200,400" fill="none" stroke="#ffffff" stroke-width="6" opacity="0.8"/>
    <path d="M620,811 C860,730 1060,640 1200,570 V811 Z" fill="url(#bandDark)" opacity="0.85"/>
  </svg>

  <div class="brand"><span class="brand-dot"></span>Hofwerk</div>

  <h1 class="product-name">
    <span class="line-one">Moss</span>
    <span class="line-two">Vanish</span>
  </h1>

  <svg class="hazard" viewBox="0 0 40 40" aria-label="Hazard pictogram" role="img">
    <path d="M20 2 L38 20 L20 38 L2 20 Z" fill="#fff" stroke="var(--hazard)" stroke-width="3"/>
    <rect x="18" y="10" width="4" height="14" fill="#111"/>
    <rect x="18" y="27" width="4" height="4" fill="#111"/>
  </svg>

  <div class="instructions">
    <h2>Wettelijk gebruiksvoorschrift:</h2>
    <p>Toegestaan is uitsluitend het gebruik als middel ter bestrijding van groene aanslag. Het behandelen van verharde oppervlakken en apparatuur naast watergangen bij de bestrijding van groene aanslag is niet toegestaan. Dit middel is giftig voor vissen en andere waterorganismen. Voorkomen moet worden dat de vloeistof het oppervlaktewater bereikt.</p>
    <h2>Gebruiksaanwijzing:</h2>
    <p>Ter verwijdering en ter voorkoming van groene aanslag op muren, daken, tegelpaden, flagstones, grafzerken, ramen, bielsen, tuinmeubelen e.d. Spuiten, gieten, borstelen of schrobben met een oplossing van<br>2,5% van dit middel (25 ml op 1 liter water). Niet naspoelen.<br>Niet op planten spuiten of gieten.</p>
    <p class="gap">Houd huisdieren weg van de behandelde plekken, zolang deze nog vochtig zijn.<br>
    <strong>Opmerking:</strong> Het middel wordt onwerkzaam wanneer het in contact komt met zeep of synthetische wasmiddelen. <strong>Aard van het preparaat:</strong> vloeistof<br>
    Werkzame stof(fen): didecyldimethylammoniumchloride.<br>
    Gehalte: 100 g/l. Andere zeer giftige, giftige, bijtende of schadelijke stof(fen): ---</p>
  </div>

  <div class="registration">Toelatingsnummer: 20871 N</div>
</div>
</body>
</html>
```